Marwick Family Chiropractic Stationary

The letterhead and business card must have our logo.
We would like to see the logo used in different ways ( It can be expanded upon in the stationary.)
Please use the the same or similar colors.
Must be eye catching and memorable.
Must be easy to read

Reason: The doctor has been too busy to make any final decisions. He would like to give himself a little more time.

Target Market(s)

Chiropractic Healthcare

Industry/Entity Type

Business

Requirements
Must have
• Dr. Leonard Marwick D.C.
Chiropractor

860-555-0183

417 Birchfield Road, 2nd Floor
Halbrook, CT 06091

drmarwick@marwickspine.example
www.marwickspine.example
www.facebook.com/MarwickFamilySpine
Should not have
• should not be difficult to read

```html
<!DOCTYPE html>
<html lang="en">
<head>
<meta charset="utf-8">
<title>Marwick Family Chiropractic — Business Cards</title>
<link rel="stylesheet" href="https://fonts.googleapis.com/css2?family=Questrial&family=Montserrat:wght@600;700&family=Arimo:wght@400;700&display=swap">
<style>
  :root {
    --backdrop: #e6e2dc;
    --card-black: #000000;
    --leaf-green: #a6cc54;
    --bark-grey: #a29a8e;
    --text-white: #ffffff;
    --text-soft: #9a948a;
    --divider: #6b6b6b;
    --pattern-dark: #141a10;
    --pattern-mid: #27301b;
  }
  * { box-sizing: border-box; margin: 0; padding: 0; }
  html, body { width: 1200px; height: 724px; overflow: hidden; }
  body { background: var(--backdrop); position: relative; font-family: "Arimo", Arial, sans-serif; }

  .card { position: absolute; overflow: hidden; }
  .card--details { left: 40px; top: 39px; width: 543px; height: 311px; background: var(--card-black); }
  .card--mark    { left: 616px; top: 38px; width: 543px; height: 309px; background: var(--card-black); }
  .card--pattern { left: 40px; top: 374px; width: 545px; height: 311px; background: var(--card-black); }
  .card--green   { left: 617px; top: 370px; width: 543px; height: 310px; background: var(--leaf-green); }

  .brand-name { font-family: "Montserrat", "Century Gothic", sans-serif; font-weight: 700; text-align: center; line-height: 1; color: var(--leaf-green); }
  .brand-name__main { display: block; }
  .brand-name__sub { display: block; color: var(--bark-grey); font-weight: 600; }

  /* front card */
  .brand-block { position: absolute; left: 18px; top: 14px; width: 170px; }
  .brand-dot { display: block; width: 86px; height: 86px; border-radius: 50%; background: var(--leaf-green); margin: 0 auto 16px; }
  .brand-block .brand-name__main { font-size: 26px; letter-spacing: 0.5px; }
  .brand-block .brand-name__sub { font-size: 10.5px; letter-spacing: 0.3px; margin-top: 6px; }

  .doctor { position: absolute; left: 30px; top: 192px; color: var(--text-white); }
  .doctor__name { font-weight: 700; font-size: 16px; color: var(--leaf-green); }
  .doctor__role { font-size: 14px; color: var(--text-soft); margin-top: 6px; }
  .doctor__address { font-size: 13.5px; line-height: 22px; margin-top: 8px; font-style: normal; }

  .divider { position: absolute; left: 262px; top: 193px; width: 1px; height: 103px; background: var(--divider); }

  .contact-list { position: absolute; left: 276px; top: 186px; list-style: none; }
  .contact-list li { height: 27.5px; display: flex; align-items: center; gap: 7px; color: var(--text-white); font-size: 13.5px; }
  .contact-list svg { width: 11px; height: 11px; flex: none; }
  .contact-list .square { width: 10px; height: 10px; background: var(--leaf-green); flex: none; }

  /* mark cards */
  .centre-name { position: absolute; left: 0; right: 0; top: 100px; }
  .centre-name .brand-name__main { font-size: 48px; letter-spacing: 1.5px; }
  .centre-name .brand-name__sub { font-size: 17px; letter-spacing: 1px; margin-top: 12px; }
  .card--green .centre-name, .card--green .centre-name .brand-name__sub { color: var(--text-white); }

  .site-url { position: absolute; left: 0; right: 0; text-align: center; font-family: "Questrial", "Century Gothic", sans-serif; font-size: 15px; letter-spacing: 2px; color: var(--text-white); line-height: 18px; }
  .card--mark .site-url { top: 260px; }
  .card--green .site-url { top: 249px; }
  .card--pattern .site-url { top: 249px; }

  /* pattern card */
  .pattern-fill { position: absolute; inset: 0; background: radial-gradient(circle at 50% 50%, var(--pattern-mid), var(--pattern-dark) 75%); }
  .pattern-name { position: absolute; left: 0; right: 0; top: 82px; }
  .pattern-name .brand-name__main { font-size: 64px; letter-spacing: 2px; }
  .pattern-name .brand-name__sub { font-size: 27px; letter-spacing: 1px; margin-top: 14px; }
</style>
</head>
<body>

  <section class="card card--details" aria-label="Business card front">
    <div class="brand-block">
      <span class="brand-dot"></span>
      <p class="brand-name"><span class="brand-name__main">MARWICK</span><span class="brand-name__sub">FAMILY CHIROPRACTIC</span></p>
    </div>

    <div class="doctor">
      <p class="doctor__name">Dr. Leonard Marwick D.C.</p>
      <p class="doctor__role">Chiropractor</p>
      <address class="doctor__address">417 Birchfield Road, 2nd Floor<br>Halbrook, CT 06091</address>
    </div>

    <div class="divider"></div>

    <ul class="contact-list">
      <li>
        <svg viewBox="0 0 12 12" aria-hidden="true"><path d="M2.5 1 L4.5 1 L5.2 3.6 L4 4.6 C4.7 6 6 7.3 7.4 8 L8.4 6.8 L11 7.5 L11 9.5 C11 10.3 10.3 11 9.5 11 C5 11 1 7 1 2.5 C1 1.7 1.7 1 2.5 1Z" fill="none" stroke="#a6cc54" stroke-width="1.2"/></svg>
        860-555-0183
      </li>
      <li>
        <svg viewBox="0 0 12 12" aria-hidden="true"><rect x="0.5" y="2.5" width="11" height="7.5" fill="#a6cc54"/><path d="M0.5 2.5 L6 7 L11.5 2.5" fill="none" stroke="#000" stroke-width="1"/></svg>
        mymarwick@marwickspine.example
      </li>
      <li>
        <svg viewBox="0 0 12 12" aria-hidden="true"><circle cx="6" cy="6" r="5.2" fill="none" stroke="#a6cc54" stroke-width="1.1"/><ellipse cx="6" cy="6" rx="2.3" ry="5.2" fill="none" stroke="#a6cc54" stroke-width="1"/><line x1="0.8" y1="6" x2="11.2" y2="6" stroke="#a6cc54" stroke-width="1"/></svg>
        www.marwickspine.example
      </li>
      <li>
        <span class="square"></span>
        MarwickFamilySpine
      </li>
    </ul>
  </section>

  <section class="card card--mark" aria-label="Business card back, dark">
    <p class="brand-name centre-name"><span class="brand-name__main">MARWICK</span><span class="brand-name__sub">FAMILY CHIROPRACTIC</span></p>
    <p class="site-url">www.marwickspine.example</p>
  </section>

  <section class="card card--pattern" aria-label="Business card back, patterned">
    <div class="pattern-fill" role="img" aria-label="Repeating pattern of small dark tree marks in muted green and brown"></div>
    <p class="brand-name pattern-name"><span class="brand-name__main">MARWICK</span><span class="brand-name__sub">FAMILY CHIROPRACTIC</span></p>
    <p class="site-url">www.marwickspine.example</p>
  </section>

  <section class="card card--green" aria-label="Business card back, green">
    <p class="brand-name centre-name"><span class="brand-name__main">MARWICK</span><span class="brand-name__sub">FAMILY CHIROPRACTIC</span></p>
    <p class="site-url">www.marwickspine.example</p>
  </section>

</body>
</html>
```